Counseling Practice Business Card

I need a professional looking business card incorporating my new logo that was just completed. Card needs to incorporate my name and title, description of my specialty, my address, my phone number, my fax number, my email and my website URL. I need to be able to choose design on/with different paper colors and textures.
I do not have a lot of business card ideas so I am open to anything but I want bold,sharp, clear card without additional designs other than my logo (see attached file info). I am open to different color backgrounds or paper colors including black. I do not like traditional brackets around area codes in phone number or dashes between numbers in phone number. Am open to other ways of presenting including periods between numbers as appropriate. I do not know enough to know what I like yet but I want card to coordinate and work together with my logo. My practice emphasizes natural mental health interventions so any use of color (with background paper color or the blue and green in my logo) that elicits nature is nice. In addition to black, any natural brown or wood looking background might be desirable also. Most of the offerings so far look very similar and boring.

Target Market(s)

Potential therapy clients and other professionals

Contact Information for Business Card

Card information:
Gerald M. Whitcombe, Ph.D.
Licensed Clinical Psychologist
Integrative Health Coach
4812 Marlowe Ridge Blvd SE
Suite 310
Fernbrook, GA 31204
(770) 415-2983 phone
(770) 581-4096 fax
drgeraldwhitcombe@quillmarsh.net
brightfernwellness.net

Font styles to use
Serif
Sans Serif
Other font styles liked:
• anything that you think looks crisp, clear and easily readable

Requirements
Must have
• Any color used should coordinate with my logo design (see attached files).
• Card should be printed horizontally so top and bottom are longest sides of rectangle.
• Background color or paper color should complement and highlight logo. Do not like a white background. black, grey, brown or any color my logo would blend well with.
Nice to have
• I would like designer to utilize color to highlight letters/name or phone-fax-web symbols.
• Bottom edge of card could be highlighted if appropriate to an idea.
Should not have
• I would NOT want the card to have a pure white background at all.
• No clear cards.
• Cards should be oriented with long sides on bottom and top, NOT sides. DO NOT LIKE THIS THIN TALL ORIENTATION.

```html
<!DOCTYPE html>
<html lang="en">
<head>
<meta charset="utf-8">
<title>Brightfern Wellness – Business Card</title>
<link href="https://fonts.googleapis.com/css2?family=Jost:wght@300;400;500;600&display=swap" rel="stylesheet">
<style>
  :root {
    --stage: #e9e4de;
    --card-back: #5b4641;
    --card-face: #c7a882;
    --band: #4f3c37;
    --brand-brown: #6e4f42;
    --ink: #3f3430;
    --light: #fbf7f2;
    --shadow: rgba(40, 28, 22, 0.28);
  }
  * { box-sizing: border-box; margin: 0; padding: 0; }
  html, body {
    width: 1200px; height: 900px; overflow: hidden;
    background: var(--stage);
    font-family: "Jost", "Helvetica Neue", Arial, sans-serif;
  }
  .stage { position: relative; width: 1200px; height: 900px; }
  .card {
    position: absolute; left: 280px; width: 640px; height: 366px;
    border-radius: 4px; overflow: hidden;
    box-shadow: 0 14px 30px var(--shadow);
  }
  /* Back of card */
  .card-back {
    top: 64px; background: var(--card-back);
    display: flex; align-items: center; justify-content: center;
  }
  .card-back .brand-name {
    color: var(--light); font-size: 46px; font-weight: 500; letter-spacing: 1px;
  }
  /* Front of card */
  .card-front {
    top: 470px;
    background: radial-gradient(ellipse at 55% 45%, #cfb18c 0%, var(--card-face) 70%);
  }
  .name-band {
    position: absolute; left: 0; top: 46px; width: 392px; height: 42px;
    background: var(--band);
  }
  .band-end {
    position: absolute; right: 0; top: 46px; width: 34px; height: 42px;
    background: var(--band); border-radius: 20px 0 0 20px;
  }
  .practitioner-name {
    position: absolute; left: 32px; top: 53px;
    color: var(--light); font-size: 21px; font-weight: 600; white-space: nowrap;
  }
  .card-front .brand-name {
    position: absolute; left: 400px; width: 200px; top: 51px; text-align: center;
    color: var(--brand-brown); font-size: 22px; font-weight: 500; line-height: 32px;
    white-space: nowrap;
  }
  .credentials { position: absolute; left: 32px; top: 96px; color: var(--ink); }
  .credentials .license { font-size: 13px; font-weight: 300; }
  .credentials .specialty { font-size: 15px; font-weight: 500; margin-top: 1px; }
  .contact-list {
    position: absolute; left: 30px; bottom: 26px; list-style: none; color: var(--light);
  }
  .contact-list li {
    display: flex; align-items: center; gap: 10px;
    font-size: 16px; font-weight: 400; line-height: 23px; white-space: nowrap;
  }
  .contact-list svg { width: 14px; height: 14px; fill: var(--band); flex: none; }
  .address {
    position: absolute; right: 32px; bottom: 26px; text-align: right;
    color: var(--light); font-size: 17px; font-weight: 600; line-height: 24px;
    font-style: normal; white-space: nowrap;
  }
</style>
</head>
<body>
<main class="stage">
  <section class="card card-back" aria-label="Card back">
    <span class="brand-name">Brightfern Wellness</span>
  </section>

  <section class="card card-front" aria-label="Card front">
    <div class="name-band"></div>
    <div class="band-end"></div>
    <h1 class="practitioner-name">Gerald M. Whitcombe, Ph.D.</h1>
    <span class="brand-name">Brightfern Wellness</span>

    <div class="credentials">
      <p class="license">Licensed Clinical Psychologist</p>
      <p class="specialty">Integrative Health Coach</p>
    </div>

    <ul class="contact-list">
      <li>
        <svg viewBox="0 0 24 24" aria-label="Phone"><path d="M6.6 10.8a15.1 15.1 0 0 0 6.6 6.6l2.2-2.2c.3-.3.7-.4 1-.2 1.1.4 2.3.6 3.6.6.6 0 1 .4 1 1V20c0 .6-.4 1-1 1C10.6 21 3 13.4 3 4c0-.6.4-1 1-1h3.5c.6 0 1 .4 1 1 0 1.3.2 2.5.6 3.6.1.3 0 .7-.2 1z"/></svg>
        (770) 415-2983
      </li>
      <li>
        <svg viewBox="0 0 24 24" aria-label="Fax"><path d="M7 3h8l3 3v4H7zM4 11h16a1 1 0 0 1 1 1v8a1 1 0 0 1-1 1H4a1 1 0 0 1-1-1v-8a1 1 0 0 1 1-1zm3 3v2h2v-2zm4 0v2h2v-2zm4 0v2h2v-2zm-8 3v2h2v-2zm4 0v2h2v-2z"/></svg>
        (770) 581-4096
      </li>
      <li>
        <svg viewBox="0 0 24 24" aria-label="Email"><path d="M12 2a10 10 0 1 0 5 18.7l-1-1.7A8 8 0 1 1 20 12v1a2 2 0 0 1-4 0V7h-2v1a5 5 0 1 0 .9 7.3A4 4 0 0 0 22 13v-1A10 10 0 0 0 12 2zm0 13a3 3 0 1 1 0-6 3 3 0 0 1 0 6z"/></svg>
        drgeraldwhitcombe@quillmarsh.net
      </li>
      <li>
        <svg viewBox="0 0 24 24" aria-label="Website"><path d="M12 2a10 10 0 1 0 0 20 10 10 0 0 0 0-20zm6.9 6h-3a15 15 0 0 0-1.3-3.9A8 8 0 0 1 18.9 8zM12 4c.8 1.2 1.5 2.5 1.9 4h-3.8c.4-1.5 1.1-2.8 1.9-4zM4.3 14a8 8 0 0 1 0-4h3.4a16 16 0 0 0 0 4zm.8 2h3a15 15 0 0 0 1.3 3.9A8 8 0 0 1 5.1 16zm3-8h-3a8 8 0 0 1 4.3-3.9A15 15 0 0 0 8.1 8zM12 20c-.8-1.2-1.5-2.5-1.9-4h3.8c-.4 1.5-1.1 2.8-1.9 4zm2.3-6H9.7a14 14 0 0 1 0-4h4.6a14 14 0 0 1 0 4zm.3 5.9a15 15 0 0 0 1.3-3.9h3a8 8 0 0 1-4.3 3.9zm1.7-5.9a16 16 0 0 0 0-4h3.4a8 8 0 0 1 0 4z"/></svg>
        brightfernwellness.net
      </li>
    </ul>

    <address class="address">
      4812 Marlowe Ridge Blvd SE<br>
      Suite 310<br>
      Fernbrook, GA 31204
    </address>
  </section>
</main>
</body>
</html>
```